ELsewhen website redesign to provide information about experiential workshops, film work and other

We need a redesign of our website elsewhen.org. We conduct experiential workshops of discovery and transformation for individuals and organizations. We need the website to reflect the full extent of ELsewhen programs, and be an information hub for ELsewhen workshops and communities as they develop.

The attached documents contain information about the organization - it's brandbook, copy for web pages, a website layout and a couple of images.

The site is for individuals and companies looking to promote and be change to make a difference. It should be warm, welcoming, and create excitement around the concepts and the ability to discover a new way of being in the world. We are about creating communities around the globe who will embody play, freedom, curiosity and expanded possibilities. We are creating a space for this to happen, both physically (workshops) and online.

We will be on either a SquareSpace, but mos tlikely a Weebly plaform.

Please look at the current site at www.elsewhen.org

Target Market(s)

Initially, are target market will be baby boomers, but will expand to include millennials and students.

Coding

Coded - Design and coding required

Number of Pages Required

5+ page

Requirements
Must have
• The colors, logo and fonts from the brand book.
Nice to have
• Complimentary use of brand colors to create an attractive presentation and energy

```html
<!DOCTYPE html>
<html lang="en">
<head>
<meta charset="utf-8">
<title>ELsewhen</title>
<link href="https://fonts.googleapis.com/css2?family=Jost:wght@300;400;500;600;700&family=Poppins:wght@300;400;500;600&display=swap" rel="stylesheet">
<style>
:root{
  --orange:#f26430;
  --orange-soft:#f07a4a;
  --green:#8fce8a;
  --dark:#111111;
  --hero-dark:#2a2a2a;
  --grey-band:#efefef;
  --ink:#1b1b1b;
  --muted:#555555;
  --cream:#fdf0d5;
  --white:#ffffff;
}
*{box-sizing:border-box;margin:0;padding:0}
html,body{width:1200px;height:3838px;overflow:hidden}
body{font-family:"Poppins",sans-serif;color:var(--ink);background:var(--white);position:relative}
h1,h2,h3,h4{font-family:"Jost",sans-serif;font-weight:500}
section,header,footer{position:absolute;left:0;width:1200px}

/* Hero */
.hero{top:0;height:614px;background:var(--hero-dark);overflow:hidden}
.hero-photo{position:absolute;inset:0;background:linear-gradient(120deg,#1d1d1d 0%,#3a3632 45%,#2c2a28 100%)}
.hero-diagonal{position:absolute;inset:0}
.topbar{position:absolute;top:40px;left:133px;right:133px;height:40px;display:flex;align-items:center}
.brand{font-family:"Jost",sans-serif;font-weight:600;font-size:30px;letter-spacing:4px;color:var(--white)}
.topbar-actions{margin-left:auto;display:flex;gap:14px;align-items:center}
.pill{border:2px solid var(--white);border-radius:20px;color:var(--white);font-size:13px;font-weight:600;padding:6px 16px;display:flex;gap:7px;align-items:center;letter-spacing:.5px}
.menu-icon{margin-left:6px}
.hero-left{position:absolute;left:133px;top:236px;font-size:42px;line-height:52px;color:var(--white)}
.hero-left span{color:var(--orange)}
.hero-right{position:absolute;right:133px;top:384px;text-align:right;font-size:42px;line-height:52px;color:var(--white)}
.hero-right span{color:var(--green);font-weight:400}

/* Discover */
.discover{top:614px;height:486px;text-align:center}
.discover h2{margin-top:62px;font-size:35px;line-height:46px;font-weight:500}
.discover h2 span{display:block;font-weight:400}
.benefits{position:absolute;top:205px;left:0;width:1200px}
.benefit{position:absolute;width:200px;text-align:center;font-size:16px;line-height:24px}
.benefit svg{display:block;margin:0 auto 18px}

/* Vision */
.vision{top:1100px;height:505px;background:var(--grey-band)}
.framed-photo{position:absolute;border:3px solid var(--orange);padding:10px}
.framed-photo .fill{width:100%;height:100%;border:2px solid rgba(255,255,255,.8)}
.copy{position:absolute;font-size:13.5px;line-height:26px;color:var(--muted)}
.copy h2{font-size:44px;color:var(--ink);margin-bottom:22px;line-height:48px}
.copy p+p{margin-top:18px}

/* What we do */
.what{top:1605px;height:617px}
.what h3{font-family:"Poppins",sans-serif;font-size:17px;font-weight:400;color:var(--ink);margin:-12px 0 12px}
.movements-art{width:374px;height:58px;margin-top:26px;background:#e6e6e6;border-radius:4px}
.movement-labels{display:flex;width:374px;margin-top:8px}
.movement-labels span{flex:1;text-align:center;font-size:7px;font-weight:600;color:var(--ink);white-space:nowrap;line-height:10px}

/* Unsettling the calm */
.peace{top:2222px;height:530px;background:var(--orange-soft);overflow:hidden}
.peace-bg{position:absolute;inset:0;background:linear-gradient(90deg,#e8693a,#f28457 60%,#ef7a4b)}
.peace-frame{position:absolute;left:123px;top:80px;width:414px;height:345px;border:3px solid rgba(255,255,255,.85)}
.peace-photo{position:absolute;left:141px;top:95px;width:412px;height:351px;background:linear-gradient(160deg,#5a5854,#2f2d2b 55%,#6d6a66)}
.peace .copy{color:var(--white);left:609px;top:96px;width:458px}
.peace .copy h2{color:var(--white)}

/* Community */
.community{top:2752px;height:512px;text-align:center}
.community h2{margin-top:82px;font-size:42px}
.community p{margin-top:16px;font-size:17px;line-height:30px;color:#333}

/* Footer */
.footer{top:3264px;height:486px;background:var(--dark);color:var(--white)}
.footer h4{font-size:22px;font-weight:500;margin-bottom:24px}
.col{position:absolute;top:170px;font-size:11.5px;line-height:19px}
.contact-row{display:flex;gap:18px;margin-bottom:18px;align-items:flex-start}
.email-input{width:262px;height:34px;border-radius:17px;background:var(--white);color:#888;font-size:10px;padding:10px 18px;margin:20px 0 14px}
.subscribe{display:inline-block;border:2px solid var(--white);border-radius:16px;padding:5px 18px;font-size:11px;font-weight:600}
.links li{list-style:none;font-size:11px;line-height:26px}
.footer-brand{font-family:"Jost",sans-serif;font-weight:600;font-size:22px;letter-spacing:3px}
.socials{display:flex;gap:10px;margin-top:30px}
.socials span{width:26px;height:26px;border:1.5px solid var(--white);border-radius:50%}

/* Form */
.enquiry{position:absolute;left:269px;top:3008px;width:660px;height:352px;background:var(--cream);box-shadow:0 6px 20px rgba(0,0,0,.18);padding:40px 34px 0;display:grid;grid-template-columns:1fr 1fr;column-gap:26px;row-gap:20px;align-content:start}
.field label{display:block;font-size:11px;color:#333;margin-bottom:8px}
.field .box{height:34px;background:var(--white);border:1px solid #d6c9ad;font-size:10px;display:flex;align-items:center;padding-left:10px;color:#555}
.continue{height:36px;background:var(--orange);color:var(--white);font-size:12px;font-weight:600;display:flex;align-items:center;justify-content:center;margin-top:6px}

.legal{position:absolute;top:3750px;left:0;width:1200px;height:88px;background:var(--dark);border-top:1px solid #2b2b2b;color:#ddd;text-align:center;font-size:11.5px;line-height:88px}
</style>
</head>
<body>

<header class="hero">
  <div class="hero-photo" role="img" aria-label="Workshop participants gathered in a dimly lit gallery room"></div>
  <svg class="hero-diagonal" width="1200" height="614" viewBox="0 0 1200 614">
    <polygon points="770,0 1200,0 1200,614 420,614" fill="#ffffff" fill-opacity="0.12"/>
    <polygon points="0,0 770,0 420,614 0,614" fill="#000000" fill-opacity="0.35"/>
  </svg>
  <div class="topbar">
    <div class="brand">ELSEWHEN</div>
    <div class="topbar-actions">
      <span class="pill"><svg width="12" height="9" viewBox="0 0 12 9"><rect width="12" height="9" rx="1" fill="#fff"/><path d="M0 0l6 5 6-5" stroke="#2a2a2a" fill="none"/></svg>EMAIL</span>
      <span class="pill"><svg width="10" height="12" viewBox="0 0 10 12"><rect y="5" width="10" height="7" rx="1" fill="#fff"/><path d="M2.5 5V3.5a2.5 2.5 0 015 0V5" stroke="#fff" stroke-width="1.5" fill="none"/></svg>MEMBER LOGIN</span>
      <svg class="menu-icon" width="30" height="24" viewBox="0 0 30 24"><rect width="30" height="4" rx="2" fill="#fff"/><rect y="10" width="30" height="4" rx="2" fill="#fff"/><rect y="20" width="30" height="4" rx="2" fill="#fff"/></svg>
    </div>
  </div>
  <h1 class="hero-left">What World Do We<br><span>Want to Live In?</span></h1>
  <h1 class="hero-right"><span>What Kind of Life</span><br>Do You Want to Create?</h1>
</header>

<section class="discover">
  <h2>Discover an Opportunity to Live a More<span>Dynamic and Meaningful Life</span></h2>
  <div class="benefits">
    <div class="benefit" style="left:84px">
      <svg width="104" height="104" viewBox="0 0 104 104"><circle cx="52" cy="52" r="49" fill="none" stroke="#f26430" stroke-width="4"/><circle cx="40" cy="32" r="6" fill="#f26430"/><circle cx="64" cy="32" r="6" fill="#f26430"/><path d="M40 40l-6 18 4 16M40 40l6 14-4 20M64 40l-6 14 8 20M64 40l6 18-6 16M34 46l-8 8M70 46l8 8" stroke="#f26430" stroke-width="5" stroke-linecap="round" fill="none"/></svg>
      Moves Energy
    </div>
    <div class="benefit" style="left:284px">
      <svg width="104" height="104" viewBox="0 0 104 104"><circle cx="52" cy="52" r="49" fill="none" stroke="#f26430" stroke-width="4"/><rect x="44" y="28" width="16" height="12" fill="#f26430"/><rect x="26" y="62" width="14" height="12" fill="#f26430"/><rect x="45" y="62" width="14" height="12" fill="#f26430"/><rect x="64" y="62" width="14" height="12" fill="#f26430"/><path d="M52 40v22M33 62v-10h38v10" stroke="#f26430" stroke-width="3" fill="none"/></svg>
      Creates Opportunities<br>for Connecting
    </div>
    <div class="benefit" style="left:484px">
      <svg width="104" height="104" viewBox="0 0 104 104"><circle cx="52" cy="52" r="49" fill="none" stroke="#f26430" stroke-width="4"/><path d="M36 74V62c-6-4-9-10-8-18 2-12 12-18 24-17 13 1 22 11 21 23l4 8h-5v7c0 3-3 5-6 5h-6v8" stroke="#f26430" stroke-width="3" fill="none"/><circle cx="52" cy="46" r="7" fill="none" stroke="#f26430" stroke-width="2.5"/><path d="M52 33v5M52 54v5M39 46h5M60 46h5" stroke="#f26430" stroke-width="2.5"/></svg>
      Supports Conscious<br>Evolution
    </div>
    <div class="benefit" style="left:684px">
      <svg width="104" height="104" viewBox="0 0 104 104"><circle cx="52" cy="52" r="49" fill="none" stroke="#f26430" stroke-width="4"/><circle cx="52" cy="30" r="7" fill="#f26430"/><path d="M34 28l18 14 18-14M46 42h12v14l4 22h-6l-4-16-4 16h-6l4-22z" stroke="#f26430" stroke-width="4" stroke-linejoin="round" fill="#f26430"/></svg>
      Deepens<br>Experience of Life
    </div>
    <div class="benefit" style="left:883px">
      <svg width="104" height="104" viewBox="0 0 104 104"><circle cx="52" cy="52" r="49" fill="none" stroke="#f26430" stroke-width="4"/><rect x="33" y="36" width="38" height="24" rx="2" fill="none" stroke="#f26430" stroke-width="3.5"/><path d="M26 66h52l-4 5H30z" fill="#f26430"/></svg>
      Provides Opportunities<br>for Collaboration<br>and Creation
    </div>
  </div>
</section>

<section class="vision">
  <div class="framed-photo" style="left:141px;top:78px;width:443px;height:345px">
    <div class="fill" role="img" aria-label="Group of workshop participants seated in a circle on a rug" style="background:linear-gradient(150deg,#c7684a,#a84a32 55%,#d98063)"></div>
  </div>
  <div class="copy" style="left:635px;top:108px;width:432px">
    <h2>Vision</h2>
    <p>We envision a world in which all people and communities can challenge and break free from stories that no longer serve us. We believe that solutions to contemporary challenges will emerge from a place of curiosity, love and connection.</p>
    <p>Through inspiration, conscious reflection, and collaboration, we take responsibility for the world we are manifesting, and we can discover and create new possibilities for the lives and the society we desire to build.</p>
  </div>
</section>

<section class="what">
  <div class="copy" style="left:133px;top:124px;width:460px;color:#333">
    <h2>What We Do</h2>
    <h3>ELsewhen Life:</h3>
    <p>ELsewhen Life is a workshop designed to re-engage you with life. Through interactive exercises and personal exploration, you are taken on a journey that ultimately leaves you experiencing life as a Creator. You will learn to see beliefs and patterns that hold you back in work and relationships as well as a path to transforming the story of your life.</p>
    <p style="margin-top:10px;font-size:15px;line-height:24px;color:#222">ELsewhen Life is a 2-3 day workshop<br>experienced in 5 movements:</p>
    <div class="movements-art" role="img" aria-label="Row of five symbols, one for each workshop movement"></div>
    <div class="movement-labels"><span>Curiosity</span><span>Awareness</span><span>Owning Your Creation</span><span>Reimagining</span><span>Manifesting</span></div>
  </div>
  <div class="framed-photo" style="left:645px;top:105px;width:415px;height:397px;border:none;padding:10px;background:#5d9a72">
    <div class="fill" role="img" aria-label="Workshop circle in a wood-panelled room with large windows" style="background:linear-gradient(160deg,#6aa27e,#4e8764 60%,#7fb38f)"></div>
  </div>
</section>

<section class="peace">
  <div class="peace-bg" role="img" aria-label="Faded gallery wall behind the section"></div>
  <div class="peace-frame"></div>
  <div class="peace-photo" role="img" aria-label="Performers in costume and a singing group outdoors beside a building"></div>
  <div class="copy">
    <h2>Unsettling the Calm</h2>
    <p>The Unsettling the Calm workshop an extension of the documentary of the same name is an experiential process to transform participants into disturbers of the status quo within themselves, to enhance their relationships with others, and to change the environments in which they exist and ultimately society for the better.</p>
    <p>This workshop experience challenges us all to understand the narratives we live within, to look at our current roles in society, and to decide what role we will play to create a more humane, just and peaceful world, for all. It all starts with our willingness to unsettle the "calm" of the status quo.</p>
  </div>
</section>

<section class="community">
  <h2>In Your Community</h2>
  <p>Bring ELsewhen or the Unsettling the Calm workshop to your community.<br>We would love to hear from you.</p>
</section>

<footer class="footer">
  <div class="col" style="left:133px;width:250px">
    <h4>Contact Us</h4>
    <div class="contact-row"><svg width="14" height="18" viewBox="0 0 14 18"><path d="M7 17s6-6.5 6-10.5A6 6 0 001 6.5C1 10.5 7 17 7 17z" fill="none" stroke="#fff" stroke-width="1.4"/><circle cx="7" cy="6.5" r="2" fill="none" stroke="#fff" stroke-width="1.4"/></svg><div>ELsewhen<br>412 Lantern Row, Suite 12B<br>Millbrook, CA 90210</div></div>
    <div class="contact-row"><svg width="16" height="16" viewBox="0 0 16 16"><path d="M3 1l3 3-2 2c1 2 3 4 5 5l2-2 3 3-2 3C7 14 2 9 1 3z" fill="none" stroke="#fff" stroke-width="1.3"/></svg><div>Phone : 555 014 2290</div></div>
    <div class="contact-row"><svg width="16" height="12" viewBox="0 0 16 12"><rect x=".7" y=".7" width="14.6" height="10.6" fill="none" stroke="#fff" stroke-width="1.3"/><path d="M1 1l7 6 7-6" fill="none" stroke="#fff" stroke-width="1.3"/></svg><div>info@elsewhen.org</div></div>
  </div>
  <div class="col" style="left:417px;width:290px">
    <h4>Sign Up To Receive Email</h4>
    <p style="font-size:10.5px;line-height:17px">Excepteur sint occaecat cupidatat non proident, sunt in culpa qui nemo enim ipsam voluptatem</p>
    <div class="email-input">Enter Email</div>
    <span class="subscribe">SUBSCRIBE</span>
  </div>
  <div class="col" style="left:768px;width:160px">
    <h4>Quick Links</h4>
    <ul class="links"><li>Home</li><li>About Us</li><li>Workshops</li><li>ELsewhen Projects</li><li>Films</li><li>Store &amp; Resources</li><li>Community</li><li>Contact Us</li></ul>
  </div>
  <div class="col" style="left:952px;top:180px">
    <div class="footer-brand">ELSEWHEN</div>
    <div class="socials"><span></span><span></span><span></span></div>
  </div>
</footer>

<form class="enquiry" aria-label="Workshop enquiry">
  <div class="field"><label>First name</label><div class="box"></div></div>
  <div class="field"><label>Last name</label><div class="box"></div></div>
  <div class="field"><label>Email</label><div class="box"></div></div>
  <div class="field"><label>Phone</label><div class="box">+1 ▾</div></div>
  <div class="field"><label>Workshops</label><div class="box"></div></div>
  <div class="field"><label>Message</label><div class="box"></div></div>
  <div class="continue">CONTINUE</div>
</form>

<div class="legal">Copyright © ELsewhen 2018. All rights reserved. Terms of Service | Privacy Policy</div>

</body>
</html>
```